full stationary design for a modern sleek design company

we are a design company that does modern minimalistic interior design works as well as other design services for high end clients.
we need a full stationary design including and not limited to (double sided business card, letter head, envelopes, documents folder...etc) that reflects the modern style design we do.
sleek modern and minimalistic is the requirements.
Updates

please use the latest attached files as there was a slight modification on the logo Added Wednesday, March 1, 2017

minor update on the logo files in JPG and PSD has been updated kindly follow the new attachments. Added Thursday, March 2, 2017

Target Market(s)

modern minimalist clients

Industry/Entity Type

Design Agency

Requirements
Must have
• the logo
Nice to have
• i like the colors in the colored 3D logo attached
Should not have
• too many colors

```html
<!DOCTYPE html>
<html lang="en">
<head>
<meta charset="utf-8">
<title>Linea Studio – Business Card</title>
<link href="https://fonts.googleapis.com/css2?family=Source+Sans+3:wght@400;600&display=swap" rel="stylesheet">
<style>
  :root {
    --backdrop: #3a3a3b;
    --card-light: #fafafa;
    --card-dark: #303132;
    --accent: #f0891e;
    --ink: #2b2b2b;
    --on-accent: #ffffff;
  }
  * { margin: 0; padding: 0; box-sizing: border-box; }
  html, body {
    width: 1200px; height: 750px; overflow: hidden;
    background: var(--backdrop);
    font-family: "Source Sans 3", "Helvetica Neue", Arial, sans-serif;
  }
  .stage { position: relative; width: 1200px; height: 750px; }
  .card {
    position: absolute; top: 228px;
    width: 461px; height: 262px;
    border-radius: 11px; overflow: hidden;
  }
  .card--front { left: 124px; background: var(--card-light); }
  .card--back { left: 618px; background: var(--card-dark); }

  .wave { position: absolute; inset: 0; width: 100%; height: 100%; }

  .brand {
    position: absolute; display: flex; align-items: center; gap: 8px;
    color: var(--accent); font-weight: 600; letter-spacing: 0.04em;
    text-transform: uppercase; white-space: nowrap;
  }
  .brand__mark { display: block; background: var(--accent); }
  .card--front .brand { left: 34px; top: 34px; font-size: 25px; }
  .card--front .brand__mark { width: 22px; height: 22px; }
  .card--back .brand {
    left: 50%; top: 50%; transform: translate(-50%, -50%); font-size: 34px; gap: 12px;
  }
  .card--back .brand__mark { width: 30px; height: 30px; }

  .person { position: absolute; left: 34px; top: 102px; }
  .person__name {
    color: var(--accent); font-weight: 600; font-size: 18px;
    text-transform: uppercase; line-height: 1.1;
  }
  .person__role { color: var(--ink); font-size: 13.5px; line-height: 1.3; }

  .contact {
    position: absolute; right: 34px; top: 125px;
    color: var(--on-accent); font-size: 12.5px; text-align: right; line-height: 17px;
  }
  .contact__address { margin-bottom: 8px; }
  .contact__list { list-style: none; }
  .contact__item { display: flex; justify-content: flex-end; align-items: center; gap: 7px; height: 17.6px; }
  .contact__icon { width: 11px; height: 11px; flex: none; }
</style>
</head>
<body>
<main class="stage">

  <section class="card card--front" aria-label="Business card front">
    <svg class="wave" viewBox="0 0 461 262" preserveAspectRatio="none" aria-hidden="true">
      <path d="M0,196 C60,222 130,222 200,184 S330,80 390,64 C420,57 445,63 461,76 L461,262 L0,262 Z" fill="var(--accent)"/>
      <path d="M0,188 C60,215 130,215 200,175 S330,70 390,55 C420,48 445,55 461,68" fill="none" stroke="var(--card-dark)" stroke-width="6"/>
    </svg>

    <div class="brand"><span class="brand__mark"></span>Linea Studio</div>

    <div class="person">
      <p class="person__name">Mara Quinn</p>
      <p class="person__role">CEO&amp;Founder</p>
    </div>

    <div class="contact">
      <p class="contact__address">2140 Alder Court<br>Fairview, Oregon 97024</p>
      <ul class="contact__list">
        <li class="contact__item">(555) 201 4418
          <svg class="contact__icon" viewBox="0 0 12 12" aria-hidden="true"><path d="M2.5 1 L4.5 1 L5.3 3.4 L4 4.4 C4.6 5.8 5.8 7 7.4 7.8 L8.4 6.6 L11 7.4 L11 9.6 C11 10.4 10.4 11 9.6 11 C5 10.6 1.4 7 1 2.4 C1 1.6 1.6 1 2.5 1 Z" fill="var(--on-accent)"/></svg>
        </li>
        <li class="contact__item">(555) 730 6152
          <svg class="contact__icon" viewBox="0 0 12 12" aria-hidden="true"><rect x="3" y="0.8" width="6" height="10.4" rx="1" fill="none" stroke="var(--on-accent)" stroke-width="1.3"/><rect x="5" y="9" width="2" height="1" fill="var(--on-accent)"/></svg>
        </li>
        <li class="contact__item">mara@lineastudio.co
          <svg class="contact__icon" viewBox="0 0 12 12" aria-hidden="true"><rect x="0.5" y="2.5" width="11" height="7.5" fill="var(--on-accent)"/><path d="M0.8 2.8 L6 6.8 L11.2 2.8" fill="none" stroke="var(--accent)" stroke-width="0.9"/></svg>
        </li>
        <li class="contact__item">www.lineastudio.co
          <svg class="contact__icon" viewBox="0 0 12 12" aria-hidden="true"><circle cx="6" cy="6" r="5.5" fill="var(--on-accent)"/><ellipse cx="6" cy="6" rx="2.2" ry="5" fill="none" stroke="var(--accent)" stroke-width="0.8"/><path d="M1 6 H11" stroke="var(--accent)" stroke-width="0.8"/></svg>
        </li>
      </ul>
    </div>
  </section>

  <section class="card card--back" aria-label="Business card back">
    <div class="brand"><span class="brand__mark"></span>Linea Studio</div>
  </section>

</main>
</body>
</html>
```